Wireless Internet Service Provider website design

We need a Internet Service Provider website that show the packages that we offer as well as the functionality where customers have the option of clicking on the various packages and be linked to a page where they can sign up for our services.
We need about 10-15 pages.
A. Integrated online store.
B. Live chat.
C. Social media page
My old website. Brightlinkradio.nyc

Example: http://plumcrestnet.com/services/residential/ Added Tuesday, June 7, 2016

Target Market(s)

Residential and small businesses

Industry/Entity Type

Internet

Coding

Coded - Design and coding required

Number of Pages Required

5+ page

Font styles to use
Serif
Sans Serif
Script

Colors
3176b5
85cae6
ffffff

Requirements
Must have
• Online store and live chat, drop down details on pricing from current website
Nice to have
• great design, functional website,

```html
<!DOCTYPE html>
<html lang="en">
<head>
<meta charset="utf-8">
<title>Brightlink Radio – Wireless Internet</title>
<link href="https://fonts.googleapis.com/css2?family=Roboto:ital,wght@0,300;0,400;0,500;0,700;1,400&display=swap" rel="stylesheet">
<style>
:root{
  --cyan:#33b8d0;
  --blue:#3176b5;
  --sky:#85cae6;
  --ink:#444;
  --muted:#9a9a9a;
  --grey-band:#ececec;
  --dark:#333333;
  --white:#ffffff;
}
*{box-sizing:border-box;margin:0;padding:0}
html,body{width:1200px;height:3191px;overflow:hidden}
body{font-family:"Roboto",Arial,sans-serif;color:var(--ink);background:var(--white);position:relative}
section,header,footer{position:absolute;left:0;width:1200px}
.abs{position:absolute}

/* header */
.site-header{top:0;height:125px;background:var(--white)}
.brand{left:78px;top:30px;display:flex;align-items:center;gap:12px}
.brand-dot{width:40px;height:40px;border-radius:50%;background:var(--blue)}
.brand-name{font-size:24px;font-weight:500;color:#555}
.topbar{top:20px;left:630px;display:flex;gap:30px;align-items:center;font-size:18px}
.topbar .phone{color:#555;display:flex;gap:8px;align-items:center}
.topbar .signup{color:var(--blue);font-weight:500;font-size:16px}
.topbar .cart{color:#555;display:flex;gap:8px;align-items:center}
.main-nav{top:64px;left:355px;display:flex;align-items:center;font-size:16px;font-weight:500;color:#555}
.main-nav a{color:inherit;text-decoration:none;padding:0 20px;line-height:44px}
.main-nav a.active{background:var(--cyan);color:var(--white);border-radius:24px;padding:0 26px}

/* hero */
.hero{top:125px;height:553px;background:linear-gradient(180deg,#c9d2dc 0%,#e9d9c6 55%,#7a4a2c 78%,#5b3520 100%)}
.hero-photo{right:0;top:0;width:620px;height:553px;background:linear-gradient(90deg,rgba(200,205,215,0) 0%,#b7bec8 40%,#8f97a3 100%)}
.hero-title{left:80px;top:140px;font-size:38px;font-weight:700;line-height:52px;color:#111;letter-spacing:1px}
.hero-text{left:80px;top:258px;width:590px;font-size:20px;line-height:28px;color:#111}
.btn{display:inline-block;background:var(--cyan);color:var(--white);border-radius:30px;font-weight:500;text-align:center}
.hero-btn{left:78px;top:363px;width:207px;height:60px;line-height:60px;font-size:19px}
.float-icon{width:74px;height:74px;border-radius:50%;background:var(--white);border:5px solid rgba(255,255,255,.6);box-shadow:0 0 0 4px rgba(120,180,220,.35)}

/* welcome */
.welcome{top:678px;height:632px;text-align:center}
.section-title{font-size:40px;font-weight:400;color:#555;letter-spacing:.5px}
.section-title span{color:var(--cyan)}
.welcome .section-title{position:absolute;top:55px;width:100%}
.welcome .lead{position:absolute;top:120px;left:170px;width:860px;font-size:14.5px;line-height:26px;color:var(--muted)}
.feature{position:absolute;width:320px;text-align:center}
.ring{width:136px;height:136px;border-radius:50%;border:5px solid var(--blue);margin:0 auto;display:flex;align-items:center;justify-content:center;background:var(--white);box-shadow:inset 0 0 0 6px var(--white),inset 0 0 0 9px var(--sky)}
.feature h3{font-size:18px;font-weight:400;color:#333;margin-top:30px;line-height:26px}
.feature .rule{width:46px;height:3px;background:var(--cyan);margin:16px auto 14px}
.feature p{font-size:14px;line-height:27px;color:var(--muted)}

/* speeds */
.speeds{top:1310px;height:453px;background:var(--grey-band)}
.speeds-head{left:310px;top:55px;display:flex;align-items:center;gap:22px}
.speeds-head .mark{width:128px;height:80px;border-radius:50%;background:var(--blue)}
.speeds-head h2{font-size:34px;font-weight:400;line-height:42px;color:#444}
.speeds-head h2 span{color:var(--cyan)}
.perk{position:absolute;top:170px;width:360px;text-align:center}
.perk .ring{width:104px;height:104px;border-width:4px}
.perk h3{font-size:17px;font-weight:400;color:#333;margin-top:26px}
.perk p{font-size:14px;line-height:24px;color:var(--muted);margin-top:6px}

/* plans band */
.plans-band{top:1763px;height:157px;background:var(--cyan);text-align:center}
.plans-band h2{font-size:42px;font-weight:400;color:var(--white);line-height:157px}

/* plans */
.plans{top:1920px;height:542px}
.plan-row{left:80px;top:115px;width:1040px;height:285px;border:1px solid #e2e2e2;background:var(--white)}
.plan{position:absolute;top:115px;width:260px;text-align:center}
.plan .name{color:var(--cyan);font-style:italic;font-size:21px;line-height:29px;margin-top:28px}
.plan .price{font-size:36px;color:#333;margin-top:26px}
.plan .term{color:var(--cyan);font-style:italic;font-size:16px;margin-top:14px}
.plan .pak{font-size:21px;color:#444;margin-top:22px}
.plan .btn{width:165px;height:56px;line-height:56px;font-size:20px;margin-top:28px}
.plan-featured{position:absolute;left:600px;top:63px;width:262px;height:448px;background:var(--white);box-shadow:0 4px 12px rgba(0,0,0,.25);text-align:center}
.plan-featured .head{background:var(--cyan);color:var(--white);font-style:italic;font-size:21px;line-height:30px;padding:22px 20px;height:104px}
.plan-featured p{font-size:13.5px;line-height:24px;color:var(--muted);padding:0 26px}
.plan-featured h4{font-size:20px;font-weight:400;color:var(--cyan);margin:14px 0 8px}
.plan-featured li{list-style:none;font-size:14px;line-height:24px;color:var(--muted)}

/* testimonials */
.testimonials{top:2462px;height:388px;text-align:center}
.testimonials .section-title{position:absolute;top:60px;width:100%}
.quote-ring{position:absolute;left:569px;top:137px;width:62px;height:62px;border-radius:50%;border:3px solid var(--blue);color:var(--blue);font-size:44px;line-height:66px;font-family:Georgia,serif}
.quote-text{position:absolute;left:200px;top:212px;width:800px;font-size:15px;line-height:28px;color:#777}
.quote-name{position:absolute;top:277px;width:100%;font-size:16px;color:var(--blue)}
.quote-name small{font-size:13px}
.dots{position:absolute;top:318px;left:573px;display:flex;gap:10px}
.dots i{width:11px;height:11px;border-radius:50%;background:var(--blue);display:block}
.dots i.on{background:#222}

/* footer */
.site-footer{top:2850px;height:341px;background:var(--dark);color:#bbb}
.foot-brand{left:78px;top:90px;font-size:26px;font-weight:500;color:#b0b0b0}
.foot-brand-dot{left:160px;top:20px;width:80px;height:60px;border-radius:50%;background:var(--blue)}
.socials{left:117px;top:136px;display:flex;gap:12px}
.socials i{width:32px;height:32px;border-radius:50%;background:var(--cyan);display:block;border:2px solid #555}
.foot-col{top:38px}
.foot-col h4{font-size:17px;font-weight:400;color:var(--cyan);letter-spacing:.5px;margin-bottom:16px}
.foot-links li{list-style:none;font-size:14px;line-height:27px;color:#bbb}
.foot-links li.on{color:var(--cyan)}
.feed-item{display:flex;gap:20px;font-size:14px;line-height:27px;color:#bbb;width:240px;margin-bottom:12px}
.feed-bullet{flex:0 0 auto;margin-top:11px}
.contact-item{display:flex;gap:14px;font-size:14px;line-height:21px;color:#ddd;margin-bottom:18px}
.copyright{top:310px;width:100%;text-align:center;font-size:14px;color:#ddd}
.copyright span{color:var(--cyan)}
.email-us{right:78px;top:307px;width:145px;height:34px;background:#4a4a4a;color:#fff;font-size:16px;display:flex;align-items:center;justify-content:center;gap:10px}
</style>
</head>
<body>

<header class="site-header">
  <div class="abs brand"><span class="brand-dot"></span><span class="brand-name">Brightlink Radio</span></div>
  <div class="abs topbar">
    <span class="phone"><svg width="18" height="18" viewBox="0 0 24 24"><path fill="#33b8d0" d="M6.6 10.8a15 15 0 0 0 6.6 6.6l2.2-2.2c.3-.3.7-.4 1-.2 1.1.4 2.3.6 3.6.6.6 0 1 .4 1 1V20c0 .6-.4 1-1 1A17 17 0 0 1 3 4c0-.6.4-1 1-1h3.5c.6 0 1 .4 1 1 0 1.3.2 2.5.6 3.6.1.3 0 .7-.2 1z"/></svg>(866) 555 - 0142</span>
    <span class="signup">SIGN UP ➔</span>
    <span class="cart"><svg width="20" height="18" viewBox="0 0 24 22"><path fill="#33b8d0" d="M0 1h4l1 3h18l-3 9H7L4 3H0zM8 17a2 2 0 1 1 0 4 2 2 0 0 1 0-4zm10 0a2 2 0 1 1 0 4 2 2 0 0 1 0-4z"/></svg>Shopping cart 0</span>
  </div>
  <nav class="abs main-nav">
    <a class="active">HOME</a><a>WHY BRIGHTLINK</a><a>PLANS &amp; PACKAGES</a><a>MY ACCOUNT</a><a>GALLERY</a><a>CONTACT</a>
  </nav>
</header>

<section class="hero">
  <div class="abs hero-photo" role="img" aria-label="Photo of a young couple sitting on a wooden deck using a laptop, with a city skyline behind them"></div>
  <div class="abs float-icon" style="left:720px;top:85px"></div>
  <div class="abs float-icon" style="left:835px;top:38px"></div>
  <div class="abs float-icon" style="left:643px;top:188px"></div>
  <div class="abs float-icon" style="left:640px;top:320px"></div>
  <div class="abs float-icon" style="left:720px;top:420px"></div>
  <div class="abs float-icon" style="left:858px;top:460px"></div>
  <h1 class="abs hero-title">LOCALLY OWN, RELIABLE,<br>SUPER FAST INTRNET</h1>
  <p class="abs hero-text">Welcome to Brightlink's fiber-speed network without fiber - the new choice for those of you who don't feel you have a lot of choices.</p>
  <span class="abs btn hero-btn">SIGN UP NOW</span>
</section>

<section class="welcome">
  <h2 class="section-title">WELCOME TO <span>BRIGHTLINK RADIO</span></h2>
  <p class="lead">Brightlink radio is a highly reputable company, which is aiming at providing high quality internet access and phone services to a market that is continually growing. We are dedicated to filling the digital gap that has been created in the middle and lowe. Brightlink offers high speed internet to meet your needs at an affordable price. Finally the internet that you have been waiting for is only a click away. With Brightlink you get your money's.</p>

  <div class="feature" style="left:85px;top:262px">
    <div class="ring"><svg width="60" height="60" viewBox="0 0 60 60"><rect x="10" y="8" width="22" height="46" fill="#3176b5"/><rect x="32" y="22" width="18" height="32" fill="none" stroke="#3176b5" stroke-width="4"/><rect x="15" y="14" width="5" height="5" fill="#fff"/><rect x="23" y="14" width="5" height="5" fill="#fff"/><rect x="15" y="26" width="5" height="5" fill="#fff"/><rect x="23" y="26" width="5" height="5" fill="#fff"/><rect x="15" y="38" width="5" height="5" fill="#fff"/><rect x="23" y="38" width="5" height="5" fill="#fff"/></svg></div>
    <h3>RESIDENTIAL INTERNET<br>ACCESS</h3><div class="rule"></div>
    <p>Brightlink radio is a highly reputable company, which is aiming at providing high quality internet access and phone services to</p>
  </div>
  <div class="feature" style="left:440px;top:262px">
    <div class="ring"><svg width="64" height="64" viewBox="0 0 64 64"><path d="M8 30a24 24 0 0 0 26 26z" fill="#3176b5"/><path d="M20 44l20-20" stroke="#3176b5" stroke-width="4"/><circle cx="42" cy="22" r="4" fill="#3176b5"/><path d="M44 8a12 12 0 0 1 12 12M44 14a6 6 0 0 1 6 6" stroke="#3176b5" stroke-width="3" fill="none"/><rect x="14" y="54" width="24" height="4" fill="#3176b5"/></svg></div>
    <h3>BUSINESS INTERNET<br>ACCESS</h3><div class="rule"></div>
    <p>Brightlink radio is a highly reputable company, which is aiming at providing high quality internet access and phone services to</p>
  </div>
  <div class="feature" style="left:795px;top:262px">
    <div class="ring"><svg width="64" height="64" viewBox="0 0 64 64"><circle cx="32" cy="32" r="26" fill="none" stroke="#3176b5" stroke-width="3"/><ellipse cx="32" cy="32" rx="12" ry="26" fill="none" stroke="#3176b5" stroke-width="3"/><path d="M6 32h52M10 20h44M10 44h44" stroke="#3176b5" stroke-width="3"/><rect x="26" y="18" width="18" height="30" rx="3" fill="#fff" stroke="#3176b5" stroke-width="3"/></svg></div>
    <h3>UNLIMITED INTERNET<br>USAGE</h3><div class="rule"></div>
    <p>Brightlink radio is a highly reputable company, which is aiming at providing high quality internet access and phone services to</p>
  </div>
</section>

<section class="speeds">
  <div class="abs speeds-head">
    <span class="mark"></span>
    <h2>Fast download &amp; upload<br><span>speeds at an affordable price</span></h2>
  </div>
  <div class="perk" style="left:30px">
    <div class="ring"><svg width="48" height="48" viewBox="0 0 48 48"><circle cx="24" cy="22" r="12" fill="#3176b5"/><path d="M10 22a14 14 0 0 1 28 0" fill="none" stroke="#33b8d0" stroke-width="4"/><path d="M8 44c2-8 8-10 16-10s14 2 16 10z" fill="#3176b5"/></svg></div>
    <h3>CUSTOMER SUPPORT CENTER</h3>
    <p>Reliable and Amicable Customer Support<br>Services at Your Doorstep 24/7, 365</p>
  </div>
  <div class="perk" style="left:420px">
    <div class="ring"><svg width="46" height="46" viewBox="0 0 46 46"><circle cx="23" cy="23" r="14" fill="none" stroke="#3176b5" stroke-width="9" stroke-dasharray="6 5"/><circle cx="23" cy="23" r="12" fill="#3176b5"/><circle cx="23" cy="23" r="5" fill="#fff"/></svg></div>
    <h3>EQUIPMENT OPTIONS</h3>
    <p>a built-in 4-port full-duplex 10/100 switch to<br>connect your devices together</p>
  </div>
  <div class="perk" style="left:795px">
    <div class="ring"><svg width="46" height="46" viewBox="0 0 46 46"><rect x="6" y="20" width="8" height="20" fill="#3176b5"/><path d="M17 20l8-14c3 0 5 2 4 6l-2 6h11c3 0 4 3 3 5l-4 14c-1 2-2 3-4 3H17z" fill="#3176b5"/></svg></div>
    <h3>CUSTOMER GUARANTEE</h3>
    <p>Unlimited internet usage, you pay to get<br>internet access so use your internet to do<br>what you want.</p>
  </div>
</section>

<section class="plans-band"><h2>OUR PLANS &amp; PACKAGES</h2></section>

<section class="plans">
  <div class="abs plan-row"></div>
  <div class="plan" style="left:80px">
    <div class="name">5 Mbps Download<br>Speed</div>
    <div class="price">$39.99</div>
    <div class="term">Mo/1 Year</div>
    <div class="pak">Brightlink Simplicity</div>
    <span class="btn">KNOW MORE</span>
  </div>
  <div class="plan" style="left:340px;border-left:1px solid #e2e2e2">
    <div class="name">10 Mbps Download<br>Speed</div>
    <div class="price">$45.95</div>
    <div class="term">Mo/1 Year</div>
    <div class="pak">Brightlink Value Pak</div>
    <span class="btn">KNOW MORE</span>
  </div>
  <div class="plan" style="left:860px">
    <div class="name">25 Mbps Download<br>Speed</div>
    <div class="price">$69.99</div>
    <div class="term">Mo/1 Year</div>
    <div class="pak">Brightlink Super- Pak</div>
    <span class="btn">KNOW MORE</span>
  </div>
  <div class="plan-featured">
    <div class="head">50 Mbps Download<br>Speed</div>
    <svg width="60" height="54" viewBox="0 0 60 54" style="margin:18px 0 10px"><g stroke="#3176b5" stroke-width="2"><path d="M30 27L30 6M30 27L8 18M30 27L52 18M30 27L12 44M30 27L48 44"/></g><g fill="#33b8d0"><circle cx="30" cy="27" r="6"/><circle cx="30" cy="6" r="4"/><circle cx="8" cy="18" r="4"/><circle cx="52" cy="18" r="4"/><circle cx="12" cy="44" r="4"/><circle cx="48" cy="44" r="4"/></g></svg>
    <p>With super-fast download speeds of 50 Mbps, this is the all-in plan for anyone whose..</p>
    <h4>Includes:</h4>
    <ul><li>Free smart router</li><li>Free internet protection</li><li>Unlimited Brightlink Wi-Fi acce</li></ul>
  </div>
</section>

<section class="testimonials">
  <h2 class="section-title">WHAT OUR <span>CLIENT SAY</span></h2>
  <div class="quote-ring">“</div>
  <p class="quote-text">"By far the best customer service I have ever received from an Internet service provider. Brightlink stands above the rest, thanks for the rapid resolution to my problem."</p>
  <div class="quote-name">Dara Whitfield<small>(client)</small></div>
  <div class="dots"><i></i><i class="on"></i><i></i></div>
</section>

<footer class="site-footer">
  <div class="abs foot-brand-dot"></div>
  <div class="abs foot-brand">Brightlink Radio</div>
  <div class="abs socials"><i></i><i></i><i></i><i></i></div>

  <div class="abs foot-col" style="left:345px">
    <h4>USEFULL LINK</h4>
    <ul class="foot-links"><li class="on">Home</li><li>Why Brightlink</li><li>Plans &amp; Packages</li><li>My Account</li><li>Gallery</li><li>Contact</li></ul>
  </div>
  <div class="abs foot-col" style="left:612px">
    <h4>NEWS FEED</h4>
    <div class="feed-item"><svg class="feed-bullet" width="8" height="8" viewBox="0 0 8 8"><circle cx="4" cy="4" r="4" fill="#33b8d0"/></svg><span>Lorem ipsum is simple dummy text of print and Typesetting Industries.</span></div>
    <div class="feed-item"><svg class="feed-bullet" width="8" height="8" viewBox="0 0 8 8"><circle cx="4" cy="4" r="4" fill="#33b8d0"/></svg><span>Lorem ipsum is simple dummy text of print and Typesetting Industries.</span></div>
  </div>
  <div class="abs foot-col" style="left:875px">
    <h4>CONTACT INFO</h4>
    <div class="contact-item"><svg width="20" height="26" viewBox="0 0 20 26"><path d="M10 1a8 8 0 0 1 8 8c0 6-8 15-8 15S2 15 2 9a8 8 0 0 1 8-8z" fill="none" stroke="#33b8d0" stroke-width="2"/><circle cx="10" cy="9" r="3" fill="#33b8d0"/></svg><span>BRIGHTLINK RADIO<br>P O Box 40117 Brooklyn NY<br>11201</span></div>
    <div class="contact-item"><svg width="20" height="20" viewBox="0 0 24 24"><path fill="none" stroke="#33b8d0" stroke-width="2" d="M6.6 10.8a15 15 0 0 0 6.6 6.6l2.2-2.2c.3-.3.7-.4 1-.2 1.1.4 2.3.6 3.6.6.6 0 1 .4 1 1V20c0 .6-.4 1-1 1A17 17 0 0 1 3 4c0-.6.4-1 1-1h3.5c.6 0 1 .4 1 1 0 1.3.2 2.5.6 3.6.1.3 0 .7-.2 1z"/></svg><span>866-555-0142</span></div>
    <div class="contact-item"><svg width="22" height="16" viewBox="0 0 22 16"><rect x="1" y="1" width="20" height="14" fill="none" stroke="#33b8d0" stroke-width="2"/><path d="M1 1l10 8 10-8" fill="none" stroke="#33b8d0" stroke-width="2"/></svg><span>support@brightlinkradio.nyc</span></div>
  </div>

  <div class="abs copyright">©<span>BRIGHTLINK RADIO</span> - 2016 All rights reserved.</div>
  <div class="abs email-us"><svg width="18" height="14" viewBox="0 0 18 14"><rect x="0" y="0" width="12" height="9" fill="#fff"/><rect x="5" y="5" width="13" height="9" fill="#ddd"/></svg>Email us</div>
</footer>

</body>
</html>
```